quickdeedsale.com redesign with wireframes, white space and custom form are very important

Need a new two column design that will convert easily to mobile responsive. Lots of white space. Winning design will probably be based on header area and making the custom form stand out. I want the header to be very much like www.tallgatevk.com except the form not to go up into the header.
Here are some of the websites I really like:
www.birchdwell.com
http://ourplotpurchasedirect.com/
http://kellbrightproperty.com/

We buy homes for cash and close fast. Our target is a home seller who is desperate to sell quickly.
I have uploaded my really ugly wireframe and my logo. I also uploaded my photo for the about us box and a possible photo to use for the header.
The copy on the wireframe is what I will be using except for the about us box.

Here is the exact link for video to frame in the top left box.
https://clipvault.example/Qm38pzrtLa

0592cd
85cae6
eaf1f7
fbee3d
ec1f27

• Everything on wireframe.
• Must use Verdana font and nothing should be smaller than 12 point. Most should be in 14 point. (except maybe inside of form)

```html
<!DOCTYPE html>
<html lang="en">
<head>
<meta charset="utf-8">
<title>quickdeedsale.com — Sell your home for cash</title>
<link rel="stylesheet" href="https://fonts.googleapis.com/css2?family=Open+Sans:ital,wght@0,400;0,600;0,700;1,700&display=swap">
<style>
:root{
  --red:#ec1f27;
  --blue:#0592cd;
  --sky:#85cae6;
  --pale:#eaf1f7;
  --yellow:#fbee3d;
  --form-bg:#f8eba9;
  --page:#f6f6f6;
  --card:#ffffff;
  --ink:#2b2b2b;
  --text:#555555;
  --muted:#888888;
  --rule:#dddddd;
  --footer:#242424;
  --footer-base:#1b1b1b;
  --footer-text:#a9a9a9;
}
*{box-sizing:border-box;margin:0;padding:0}
html,body{width:1200px;height:2804px;overflow:hidden}
body{position:relative;background:var(--page);font-family:"Open Sans",Verdana,sans-serif;color:var(--text)}
.abs{position:absolute}
h2,h3{font-family:Verdana,"Open Sans",sans-serif;color:var(--ink);font-weight:700}

/* header */
.site-header{position:absolute;left:0;top:0;width:1200px;height:135px;background:#fff}
.brand{position:absolute;left:133px;top:42px;display:flex;align-items:center;gap:10px}
.brand-mark{width:26px;height:26px;background:var(--red)}
.brand-name{font-size:24px;font-weight:700;color:var(--ink)}
.call-note{position:absolute;left:832px;top:27px;font-size:13px;color:var(--text)}
.call-number{position:absolute;left:918px;top:48px;font-size:17px;font-weight:600;color:var(--ink)}
.call-icon{position:absolute;left:1040px;top:30px}
.main-nav{position:absolute;top:98px;left:538px;display:flex;gap:0;font-size:13px;color:var(--ink)}
.main-nav a{position:absolute;white-space:nowrap;text-decoration:none;color:var(--ink)}
.main-nav a.active{color:var(--red)}

/* hero */
.hero{position:absolute;left:133px;top:135px;width:934px;height:454px;
  background:linear-gradient(180deg,#2f6fc4 0%,#5e9ad8 30%,#8fb4cf 48%,#dfe3e6 55%,#cfc8bc 68%,#4f6a32 80%,#3a5424 100%)}
.hero-title{position:absolute;left:0;width:934px;top:52px;text-align:center;color:#fff;font-size:42px;font-weight:700;text-shadow:0 2px 4px rgba(0,0,0,.35)}
.hero-sub{position:absolute;left:0;width:934px;top:100px;text-align:center;color:#fff;font-size:22px;font-weight:700;text-shadow:0 1px 3px rgba(0,0,0,.35)}
.hero-arrow{position:absolute;top:350px;width:30px;height:30px;border-radius:50%;background:rgba(255,255,255,.35)}

/* form */
.offer-form{position:absolute;left:727px;top:492px;width:327px;height:489px;background:var(--form-bg);border-radius:3px}
.ribbon{position:absolute;left:663px;top:523px}
.ribbon-text{position:absolute;left:663px;top:528px;width:455px;text-align:center;color:#fff;font-size:18px;font-weight:700;font-style:italic}
.offer-sub{position:absolute;left:727px;top:562px;width:327px;text-align:center;font-size:13px;color:var(--ink)}
.field{position:absolute;left:753px;width:281px;height:30px;background:#fff;border:1px solid #efe3a3;border-radius:2px;font-size:10px;color:#777;padding:8px 0 0 34px}
.field::before{content:"";position:absolute;left:13px;top:10px;width:8px;height:8px;border-radius:50%;background:#bbb}
.submit-label{position:absolute;left:757px;top:918px;width:254px;text-align:center;color:#fff;font-size:16px;font-weight:700;letter-spacing:1px}

.privacy{position:absolute;left:727px;top:1004px;width:155px;height:28px;border:1px solid #ccc;background:#fff;font-size:11px;color:var(--ink);padding:6px 0 0 10px}
.social-sq{position:absolute;top:1002px;width:30px;height:30px}
.call-hours{position:absolute;left:727px;top:1063px;font-size:11.5px;color:var(--ink)}
.hours-rule{position:absolute;left:727px;top:1090px;width:340px;border-top:1px solid #cfcfcf}

/* sidebar cards */
.card{position:absolute;left:729px;width:338px;background:var(--card);box-shadow:0 1px 4px rgba(0,0,0,.12);padding:18px 18px}
.card h3{font-size:20px;line-height:25px;margin-bottom:12px}
.card p{font-size:11.5px;line-height:17px}
.card .who{font-weight:700;color:var(--ink);margin-top:10px}
.more-link{position:absolute;right:16px;bottom:12px;font-size:12px;color:var(--ink);display:flex;align-items:center;gap:8px}
.dot-arrow{width:13px;height:13px;border-radius:50%;background:var(--red);display:inline-block;position:relative}
.dot-arrow::after{content:"";position:absolute;left:4px;top:3.5px;border-left:5px solid #fff;border-top:3px solid transparent;border-bottom:3px solid transparent}
.ph{position:absolute}

/* left column */
.lead-title{position:absolute;left:133px;top:614px;font-size:21px}
.ticks{position:absolute;left:155px;list-style:none;font-size:13.5px;color:var(--ink)}
.ticks li{position:relative;padding-left:22px}
.ticks li::before{content:"";position:absolute;left:0;top:7px;width:7px;height:7px;border-radius:50%;background:var(--red)}
.watch-note{position:absolute;left:133px;top:735px;font-size:12px;color:var(--ink)}
.video{position:absolute;left:133px;top:777px;width:409px;height:223px;background:linear-gradient(160deg,#6aa6e0 0%,#93c3ea 35%,#274e86 55%,#b5543a 78%,#5d7f3a 100%)}
.video-play{position:absolute;left:311px;top:876px;width:30px;height:30px;background:var(--blue)}
.controls{position:absolute;left:133px;top:1004px;width:409px;height:35px;background:#fff}
.ctrl-play{position:absolute;left:0;top:0;width:35px;height:35px;background:var(--red)}
.ctrl-time{position:absolute;top:10px;font-size:10px;color:#777}
.progress{position:absolute;left:226px;top:16px;width:183px;height:4px;background:#ddd}
.progress span{display:block;width:126px;height:4px;background:#555}
.intro-bold{position:absolute;left:133px;top:1075px;width:540px;font-size:14px;line-height:21px;font-weight:700;color:var(--ink)}
.intro-text{position:absolute;left:133px;top:1124px;width:545px;font-size:12.5px;line-height:21px;color:var(--text)}
.reasons-title{position:absolute;left:133px;top:1229px;font-size:21px}
.help{position:absolute;left:133px;top:1413px;font-size:14.5px;font-weight:700;color:var(--ink)}
.dotted{position:absolute;left:133px;top:1471px;width:559px;border-top:1px dotted #bbb}
.blog-title{position:absolute;left:133px;top:1493px;font-size:20px}
.blog-more{position:absolute;left:640px;top:1498px;font-size:12px;color:var(--ink);display:flex;gap:10px;align-items:center}
.post-img{position:absolute;left:136px;width:256px;height:161px}
.post-title{position:absolute;left:411px;width:280px;font-size:14px;line-height:20px;color:var(--ink);font-weight:600}
.post-text{position:absolute;left:411px;width:280px;font-size:10px;line-height:15.5px;color:#666}
.post-meta{position:absolute;left:136px;width:556px;border-top:1px solid var(--rule);border-bottom:1px solid var(--rule);height:30px;font-size:9.5px;color:#666;padding-top:8px}
.post-meta .read{position:absolute;right:0;top:8px}
.post-meta .read::before{content:"";position:absolute;left:-26px;top:4px;border-left:4px solid #555;border-top:3px solid transparent;border-bottom:3px solid transparent}
.archives-title{position:absolute;left:133px;top:2288px;font-size:20px}
.archive-list{position:absolute;left:133px;top:2334px;list-style:none;font-size:12px;color:var(--ink)}
.archive-list li{position:relative;padding-left:25px;height:30.8px}
.archive-list li::before{content:"";position:absolute;left:0;top:3px;width:11px;height:11px;border-radius:50%;background:#444}

/* footer */
.site-footer{position:absolute;left:0;top:2521px;width:1200px;height:227px;background:var(--footer);color:var(--footer-text)}
.footer-base{position:absolute;left:0;top:2748px;width:1200px;height:56px;background:var(--footer-base)}
.f-head{position:absolute;top:36px;font-size:11.5px;font-weight:700;color:#fff;letter-spacing:.5px}
.f-text{position:absolute;font-size:10.5px;line-height:14px}
.f-links{position:absolute;left:424px;top:62px;list-style:none;font-size:10.5px;line-height:18px}
.f-links li{padding-left:20px;position:relative}
.f-links li::before{content:"";position:absolute;left:2px;top:7px;width:4px;height:4px;border-radius:50%;background:#ccc}
.contact-row{position:absolute;left:611px;font-size:10.5px;display:flex;gap:10px;align-items:center}
.newsletter-input{position:absolute;left:884px;top:109px;width:124px;height:22px;background:#fff;font-size:10px;color:#555;padding:5px 0 0 10px}
.newsletter-btn{position:absolute;left:1004px;top:109px;width:61px;height:22px;background:var(--red);color:#fff;font-size:9px;font-weight:700;text-align:center;padding-top:5px}
.copyright{position:absolute;left:135px;top:20px;font-size:10px;color:#888}
.base-dot{position:absolute;top:22px;width:12px;height:12px;border-radius:50%;background:#ccc}
</style>
</head>
<body>

<header class="site-header">
  <div class="brand"><span class="brand-mark"></span><span class="brand-name">quickdeedsale.com</span></div>
  <div class="call-note">Call us Nights and weekends ok</div>
  <div class="call-number">407-555-0148</div>
  <svg class="call-icon" width="30" height="30" viewBox="0 0 30 30" aria-hidden="true">
    <circle cx="15" cy="15" r="13" fill="none" stroke="#ec1f27" stroke-width="2.5"/>
    <path d="M10 9c1-1 2-1 2.6 0l1.2 2.2c.4.7.2 1.3-.4 1.8l-.8.7c.8 1.8 2 3 3.7 3.8l.7-.8c.5-.6 1.1-.8 1.8-.4l2.2 1.2c1 .6 1 1.6 0 2.6-1.5 1.5-3.6 1.3-6.3-.9-2.7-2.2-4.5-4.6-5-6.8-.3-1.4.2-2.6.3-3.4z" fill="#ec1f27"/>
  </svg>
  <nav class="main-nav">
    <a class="active" style="left:0">Sell Your Home</a>
    <a style="left:135px">How it works</a>
    <a style="left:254px">Stop foreclosure</a>
    <a style="left:395px">Probate</a>
    <a style="left:482px">Contact</a>
  </nav>
</header>

<section class="hero" role="img" aria-label="Photo of a single-storey white brick house with hedges under a blue sky">
  <h1 class="hero-title">Sell your home for cash in 8 days</h1>
  <p class="hero-sub">We buy Houses Nationwide</p>
  <span class="hero-arrow" style="left:24px"></span>
  <span class="hero-arrow" style="left:878px"></span>
</section>

<!-- offer form -->
<form class="offer-form"></form>
<svg class="ribbon" width="455" height="50" viewBox="0 0 455 50" aria-hidden="true">
  <polygon points="0,8 30,8 30,44 0,44 12,26" fill="#b5141b"/>
  <polygon points="455,8 425,8 425,44 455,44 443,26" fill="#b5141b"/>
  <rect x="22" y="2" width="411" height="38" fill="#ec1f27"/>
</svg>
<div class="ribbon-text">Yes, I want to sell my home fast!</div>
<div class="offer-sub">Get a no obligation written offer in 36 hours</div>
<div class="field" style="top:611px">Your Name</div>
<div class="field" style="top:651px">Your Phone number</div>
<div class="field" style="top:691px">Your Email Address</div>
<div class="field" style="top:731px">Property Address including City, State and Zip Code</div>
<div class="field" style="top:771px">Repairs needed if any</div>
<div class="field" style="top:811px">Asking price</div>
<div class="field" style="top:851px">Comments</div>
<svg class="abs" style="left:745px;top:914px" width="280" height="50" viewBox="0 0 280 50" aria-hidden="true">
  <polygon points="0,10 26,10 26,46 0,46 10,28" fill="#04699a"/>
  <polygon points="280,10 254,10 254,46 280,46 270,28" fill="#04699a"/>
  <rect x="12" y="2" width="256" height="40" fill="#0592cd"/>
</svg>
<div class="submit-label">SUBMIT</div>

<div class="privacy">Our Privacy Policy</div>
<span class="social-sq" style="left:948px;background:#2d4c8c"></span>
<span class="social-sq" style="left:993px;background:#c8402e"></span>
<span class="social-sq" style="left:1040px;background:#55acee"></span>
<div class="call-hours">Call us 8am to 10 pm Eastern time. We answer our phones</div>
<div class="hours-rule"></div>

<!-- sidebar -->
<aside class="card" style="top:1105px;height:179px">
  <h3>Home Seller Testimonials</h3>
  <p>I just wanted to thank you for buying my home in Winter Park. You made it fast and easy and kept me well informed the whole way.</p>
  <p class="who">Corwin Habel – Winter Park</p>
  <span class="more-link">More Testimonials <span class="dot-arrow"></span></span>
</aside>

<aside class="card" style="top:1299px;height:178px">
  <h3>About Us</h3>
  <div class="ph" style="left:19px;top:65px;width:82px;height:88px;background:linear-gradient(180deg,#6f8fa8,#8e7466)" role="img" aria-label="Portrait of the company owner"></div>
  <p style="position:absolute;left:114px;top:76px;width:200px">Owned and operated in Orlando Florida since 2001. Oldest Continuous operated website in country.</p>
</aside>

<aside class="card" style="top:1506px;height:354px">
  <h3>Some of the cities where we buy houses. Not all are listed.</h3>
  <p>These are the cities where we have an affiliate where you can sell a home fast or quickly and we buy homes: Orlando Jacksonville Ft Myers Tampa St Pete Gainesville Tallahassee Melbourne West Palm Beach Apopka Deland Kissimmee Lakeland Ocala Chicago Philadelphia Camden Atlanta Valdosta Houston Detroit Phoenix Seattle Tacoma Portland Charlotte Cincinnati San Antonio Harrisburg Virginia Beach Virginia Homes Greensboro Charleston SC Flint Rochester Lake Florida Wilmington Columbia Titusville If you don't see your city, we still probably buy homes there.<br>These are the types of real estate that we buy: We buy nice houses and outdated problem homes. We buy in great neighborhoods and not so nice. We buy block homes and frame homes. We buy</p>
</aside>

<aside class="card" style="top:1884px;height:256px">
  <h3>We buy nice pretty houses and some ugly ones as well.</h3>
  <div class="ph" style="left:19px;top:116px;width:149px;height:95px;background:linear-gradient(180deg,#9fc3e4,#8a8f93 55%,#5f7a45)" role="img" aria-label="Photo of a two-storey grey house"></div>
  <div class="ph" style="left:172px;top:116px;width:149px;height:95px;background:linear-gradient(180deg,#8fbbe0,#d9dcd8 50%,#5b7b3e)" role="img" aria-label="Photo of a white house with trees"></div>
</aside>

<!-- main column -->
<h2 class="lead-title">These are the benefits of selling your home to us.</h2>
<ul class="ticks" style="top:661px;line-height:21.5px">
  <li>You pick the closing date</li>
  <li>You pay NO commissions or fees</li>
  <li>You don't have to paint, clean or make repairs</li>
</ul>
<p class="watch-note">Watch to see our president Dale explain how easy it is to sell to us.</p>

<div class="video" role="img" aria-label="Video still of solar panels on a red tile roof"></div>
<span class="video-play"></span>
<svg class="abs" style="left:322px;top:884px" width="10" height="14" aria-hidden="true"><polygon points="0,0 10,7 0,14" fill="#fff"/></svg>
<div class="controls">
  <span class="ctrl-play"></span>
  <svg class="abs" style="left:13px;top:11px" width="10" height="13" aria-hidden="true"><polygon points="0,0 10,6.5 0,13" fill="#fff"/></svg>
  <span class="ctrl-time" style="left:45px">00:15:35</span>
  <span class="progress" style="left:93px;width:180px"><span style="width:126px"></span></span>
  <span class="ctrl-time" style="left:288px">2:13:35</span>
  <svg class="abs" style="left:338px;top:12px" width="30" height="12" aria-hidden="true">
    <rect x="0" y="4" width="3" height="8" fill="#0592cd"/><rect x="5" y="3" width="3" height="9" fill="#0592cd"/><rect x="10" y="2" width="3" height="10" fill="#0592cd"/><rect x="15" y="1" width="3" height="11" fill="#85cae6"/><rect x="20" y="0" width="3" height="12" fill="#ccc"/>
  </svg>
  <svg class="abs" style="left:384px;top:11px" width="14" height="14" aria-hidden="true"><path d="M1 5V1h4M9 1h4v4M13 9v4H9M5 13H1V9" stroke="#888" stroke-width="1.5" fill="none"/></svg>
</div>

<p class="intro-bold">Sell your home or house fast for cash to a professional investor company. We buy Houses and close quickly.</p>
<p class="intro-text">Selling a home on your own has never been easier. From Orlando to Greensboro - and all points in between- you can sell your home today without any hassles. Call 1-800-555-0192 or fill out the form below to get a written offer on your home in just 36 hours. Sell today online to people that care.</p>

<h2 class="reasons-title">If you need to sell a home fast because of:</h2>
<ul class="ticks" style="top:1276px;line-height:21.3px;font-size:12.5px">
  <li>Divorce or Bankruptcy</li>
  <li>Foreclosure</li>
  <li>Landlord problems - evictions with tenants okay</li>
  <li>Inherited property in probate</li>
  <li>Termites, mold, flood or fire damage, leaky roof</li>
  <li>Moving or can't afford mortgage payments</li>
</ul>
<p class="help">We Can Help. We are the fastest home buyers around.</p>
<div class="dotted"></div>

<h2 class="blog-title">Recent Blog</h2>
<span class="blog-more">More <span class="dot-arrow"></span></span>

<div class="post-img" style="top:1540px;background:linear-gradient(180deg,#5f9ad6,#d8c6a4 55%,#6d7c4b)" role="img" aria-label="Photo of a large stone villa"></div>
<h4 class="post-title" style="top:1546px">Lorem Ipsums Un Voluptas Sadips Nemis Sits Fugiat Dolores contantry</h4>
<p class="post-text" style="top:1594px">At vero eos et accusamus et iusto odios un dignissimos ducimus qui blan ditiis praesent essentum voluptatum un deleniti atquesite sites excep turiitate non providentsimils. Nemo enim ipsam voluptatem quia voluptas sit aspernatur aut odit aut fugit, consequuntur magni dolores</p>
<div class="post-meta" style="top:1724px">By Marlow &nbsp;|&nbsp; Design, Photography, Business, Corporate, Creative &nbsp;|&nbsp; 12 Comments<span class="read">Read More</span></div>

<div class="post-img" style="top:1789px;background:linear-gradient(135deg,#b9613f,#e4d2c1 50%,#7a5a44)" role="img" aria-label="Photo of a couple sitting in front of a brick house"></div>
<h4 class="post-title" style="top:1795px">Lorem Ipsums Un Voluptas Sadips Nemis Sits Fugiat Dolores contantry</h4>
<p class="post-text" style="top:1843px">At vero eos et accusamus et iusto odios un dignissimos ducimus qui blan ditiis praesent essentum voluptatum un deleniti atquesite sites excep turiitate non providentsimils. Nemo enim ipsam voluptatem quia voluptas sit aspernatur aut odit aut fugit, consequuntur magni dolores</p>
<div class="post-meta" style="top:1973px">By Marlow &nbsp;|&nbsp; Design, Photography, Business, Corporate, Creative &nbsp;|&nbsp; 12 Comments<span class="read">Read More</span></div>

<div class="post-img" style="top:2038px;background:linear-gradient(180deg,#8bb8e0,#cfc8b6 45%,#5e8a3a)" role="img" aria-label="Photo of a family running on the lawn in front of a house"></div>
<h4 class="post-title" style="top:2044px">Lorem Ipsums Un Voluptas Sadips Nemis Sits Fugiat Dolores contantry</h4>
<p class="post-text" style="top:2092px">At vero eos et accusamus et iusto odios un dignissimos ducimus qui blan ditiis praesent essentum voluptatum un deleniti atquesite sites excep turiitate non providentsimils. Nemo enim ipsam voluptatem quia voluptas sit aspernatur aut odit aut fugit, consequuntur magni dolores</p>
<div class="post-meta" style="top:2222px">By Marlow &nbsp;|&nbsp; Design, Photography, Business, Corporate, Creative &nbsp;|&nbsp; 12 Comments<span class="read">Read More</span></div>

<h2 class="archives-title">Archives</h2>
<ul class="archive-list">
  <li>Sell my house</li>
  <li>Fast cash for homes</li>
  <li>We buy houses</li>
  <li>Real Estate investor</li>
  <li>Latest</li>
</ul>

<footer class="site-footer">
  <div class="f-head" style="left:135px">WHO WE ARE</div>
  <p class="f-text" style="left:135px;top:62px;width:200px">Lorem ipsum dolor sit amet, consectetur adipiscing elit. Nullam venenatis velit blandit est condimentum aliquet. Curabitur ut libero justo. Nulla ut ex facilisis, tincidunt quam vitae, iaculis orci. Nullam eu faucibus nibh.</p>
  <span class="f-text" style="left:285px;top:162px;display:flex;gap:6px;align-items:center">More <svg width="12" height="12" aria-hidden="true"><circle cx="6" cy="6" r="5" fill="none" stroke="#aaa"/><path d="M5 3.5 7.5 6 5 8.5" stroke="#aaa" fill="none"/></svg></span>

  <div class="f-head" style="left:424px">USEFUL LINKS</div>
  <ul class="f-links">
    <li>Home</li><li>About Us</li><li>Service</li><li>FAQ</li><li>Sitemap</li><li>Contact Us</li>
  </ul>

  <div class="f-head" style="left:611px">GET IN TOUCH</div>
  <p class="f-text" style="left:611px;top:62px;width:230px">Doloreur quia commolu ptatemp dolupta oreprerum tibusam eumenis et conseet acculignis dentibea</p>
  <div class="contact-row" style="top:113px"><svg width="10" height="12" aria-hidden="true"><path d="M5 0a4 4 0 0 1 4 4c0 3-4 8-4 8S1 7 1 4a4 4 0 0 1 4-4z" fill="#ddd"/><circle cx="5" cy="4" r="1.5" fill="#242424"/></svg>84 Street, City, State 24813</div>
  <div class="contact-row" style="top:131px"><svg width="10" height="12" aria-hidden="true"><path d="M1 1c1-1 2 0 2.5 1l.8 1.5c.3.6 0 1-.4 1.4.6 1.5 1.4 2.4 2.6 3 .4-.4.8-.7 1.4-.4L9.4 9c.8.5.6 1.5-.4 2-1.5.8-3.5-.5-5.5-3S0 2 1 1z" fill="#ddd"/></svg>407-555-0148</div>
  <div class="contact-row" style="top:149px"><svg width="12" height="9" aria-hidden="true"><rect width="12" height="9" fill="#ddd"/><path d="M0 0 6 5 12 0" stroke="#242424" fill="none"/></svg>yoursite@yourmail.com</div>

  <div class="f-head" style="left:882px">NEWSLETTER SIGNUP</div>
  <p class="f-text" style="left:882px;top:62px;width:180px">Quia commolu ptatemp dolupta oreprerum tibusam</p>
  <div class="newsletter-input" style="top:109px">Email address</div>
  <div class="newsletter-btn">SUBSCRIBE</div>
</footer>
<div class="footer-base">
  <p class="copyright">© 2015 yoursite. All rights reserved.</p>
  <span class="base-dot" style="left:957px"></span>
  <span class="base-dot" style="left:980px"></span>
  <span class="base-dot" style="left:1004px"></span>
  <span class="base-dot" style="left:1054px"></span>
</div>

</body>
</html>
```